Awesome photographers card for an awesome new business

Double sided business card Black background and silver logo in middle on one side. Details on otherside. please keep it simple

Industry/Entity Type

Photographer

Contact Information for Business Card

Gerald Fenwick
0452817360
GeraldFenwickPhotography47@mailbox.test
www.GeraldFenwickPhotography.test.au
Instagram _Gerald_fenwick

Requirements
Must have
• My logo in Silver
• please use instagram logo instead of "Instagram"

```html
<!DOCTYPE html>
<html lang="en">
<head>
<meta charset="utf-8">
<title>Gerald Fenwick Photography – Business Card</title>
<link rel="stylesheet" href="https://fonts.googleapis.com/css2?family=Montserrat:wght@400;500;600&display=swap">
<style>
  :root {
    --page: #cfcfcf;
    --card-white: #f4f4f4;
    --card-black: #141414;
    --grey-dark: #6c6c6c;
    --grey-light: #d4d4d4;
    --silver: #c9c9c9;
    --logo-grey: #8a8a8a;
    --text-light: #ffffff;
  }
  * { margin: 0; padding: 0; box-sizing: border-box; }
  html, body { width: 1200px; height: 960px; overflow: hidden; }
  body {
    background: var(--page);
    font-family: "Montserrat", sans-serif;
    position: relative;
  }
  .card {
    position: absolute;
    width: 600px;
    height: 342px;
    border-radius: 14px;
    overflow: hidden;
  }
  .card--front { left: 322px; top: 126px; background: var(--card-white); }
  .card--back {
    left: 320px; top: 502px;
    background: radial-gradient(ellipse at center, #1e1e1e 0%, var(--card-black) 75%);
  }
  .card svg.card__art { position: absolute; inset: 0; }
  .contact {
    position: absolute;
    left: 31px;
    top: 200px;
    color: var(--text-light);
  }
  .contact__name {
    font-size: 18px;
    font-weight: 600;
    letter-spacing: 0.3px;
    text-transform: uppercase;
    margin-bottom: 12px;
  }
  .contact__list { list-style: none; }
  .contact__item {
    display: flex;
    align-items: center;
    gap: 10px;
    font-size: 13px;
    line-height: 19.5px;
  }
  .contact__icon { width: 14px; height: 14px; flex: none; }
  .brand {
    position: absolute;
    display: flex;
    align-items: center;
    justify-content: center;
    border-radius: 50%;
    text-align: center;
    font-weight: 500;
    text-transform: uppercase;
  }
  .brand--front {
    left: 373px; top: 52px; width: 160px; height: 160px;
    border: 3px solid var(--logo-grey);
    color: var(--logo-grey);
    font-size: 15px; letter-spacing: 2px; line-height: 1.4;
  }
  .brand--back {
    left: 199px; top: 69px; width: 202px; height: 202px;
    border: 3px solid var(--silver);
    color: var(--silver);
    font-size: 19px; letter-spacing: 2.5px; line-height: 1.4;
  }
</style>
</head>
<body>

  <section class="card card--front" aria-label="Card front with contact details">
    <svg class="card__art" viewBox="0 0 600 342" width="600" height="342" aria-hidden="true">
      <defs>
        <linearGradient id="band-fill" x1="0" y1="0" x2="1" y2="0">
          <stop offset="0" stop-color="var(--grey-dark)"/>
          <stop offset="1" stop-color="var(--grey-light)"/>
        </linearGradient>
      </defs>
      <path d="M0,12 C150,18 205,62 258,118 C338,205 375,300 585,342 L0,342 Z" fill="#b8b8b8"/>
      <path d="M0,17 C145,25 198,70 250,124 C330,208 362,305 570,342 L0,342 Z" fill="url(#band-fill)"/>
    </svg>

    <div class="brand brand--front">Gerald<br>Fenwick</div>

    <div class="contact">
      <p class="contact__name">Gerald Fenwick</p>
      <ul class="contact__list">
        <li class="contact__item">
          <svg class="contact__icon" viewBox="0 0 14 14" aria-hidden="true"><path d="M3 1 L5.5 3.5 L4 5.5 C5 7.5 6.5 9 8.5 10 L10.5 8.5 L13 11 L11 13 C6 12.5 1.5 8 1 3 Z" fill="#fff"/></svg>
          <span>0452817360</span>
        </li>
        <li class="contact__item">
          <svg class="contact__icon" viewBox="0 0 14 14" aria-hidden="true"><rect x="1" y="3" width="12" height="8" fill="#fff"/><path d="M1 3 L7 8 L13 3" fill="none" stroke="#888" stroke-width="1"/></svg>
          <span>GeraldFenwickPhotography47@mailbox.test</span>
        </li>
        <li class="contact__item">
          <svg class="contact__icon" viewBox="0 0 14 14" aria-hidden="true"><circle cx="7" cy="7" r="6" fill="#fff"/><path d="M1 7 H13 M7 1 C4 4 4 10 7 13 C10 10 10 4 7 1" fill="none" stroke="#888" stroke-width="0.9"/></svg>
          <span>www.GeraldFenwickPhotography.test.au</span>
        </li>
        <li class="contact__item">
          <svg class="contact__icon" viewBox="0 0 14 14" aria-hidden="true"><rect x="1.5" y="1.5" width="11" height="11" rx="2" fill="none" stroke="#fff" stroke-width="1.6"/></svg>
          <span>_Gerald_fenwick</span>
        </li>
      </ul>
    </div>
  </section>

  <section class="card card--back" aria-label="Card back with brand name">
    <div class="brand brand--back">Gerald<br>Fenwick</div>
  </section>

</body>
</html>
```